Print materials for 3-star hotel

We are changing up our print materials (notepads, letterheads, key card jackets, small flyer for the room rates) We are a 3 star business hotel in the Philippines and have mainly used grey tones and clean, simple lines. See attached photos for logo and hotel interior photos.

Target Market(s)

Business

Contact Information for Business Card

Corvale Terrace Hotel
Lindwell Banca Avenue corner Tolenta St Cebu City 6000 Philippines
Tel: +63 32 481 7302
Mobile: +63 917 648 2095
www.corvaleterracehotel.example

Font styles to use
Serif
Sans Serif

Requirements
Must have
• Simple
• Readable font and font size
Nice to have
• Neutral colors, grey and taupes
Should not have
• No purples and bright blues

```html
<!DOCTYPE html>
<html lang="en">
<head>
<meta charset="utf-8">
<title>Corvale Terrace Hotel — Business Card</title>
<link rel="stylesheet" href="https://fonts.googleapis.com/css2?family=Marcellus&display=swap">
<style>
  :root {
    --backdrop: #e6ebea;
    --paper: #fbfbfa;
    --paper-edge: #d9dcdb;
    --gold: #a48b66;
  }
  * { margin: 0; padding: 0; box-sizing: border-box; }
  html, body {
    width: 1200px;
    height: 900px;
    overflow: hidden;
    background: var(--backdrop);
  }
  .canvas {
    width: 1200px;
    height: 900px;
    display: flex;
    flex-direction: column;
    align-items: center;
    justify-content: center;
    gap: 60px;
    font-family: "Marcellus", serif;
    color: var(--gold);
  }
  .card {
    width: 630px;
    height: 360px;
    background: var(--paper);
    border: 1px solid var(--paper-edge);
    box-shadow: 0 10px 24px rgba(60, 70, 70, 0.12);
    position: relative;
  }

  /* Front */
  .card-front {
    display: flex;
    flex-direction: column;
    align-items: center;
    justify-content: center;
    gap: 18px;
  }
  .brand-square {
    width: 34px;
    height: 34px;
    background: var(--gold);
  }
  .brand-name {
    font-size: 24px;
    letter-spacing: 0.22em;
    text-transform: uppercase;
    text-align: center;
    line-height: 1.5;
  }

  /* Back */
  .card-back { padding: 46px 56px; }
  .contact {
    position: absolute;
    top: 46px;
    left: 230px;
  }
  .contact-name {
    font-size: 26px;
    letter-spacing: 0.06em;
    text-transform: uppercase;
    line-height: 1;
  }
  .contact-role {
    font-size: 17px;
    margin-top: 4px;
  }
  .contact-lines {
    font-size: 15px;
    line-height: 1.35;
    margin-top: 22px;
  }
  .contact-lines + .contact-lines { margin-top: 16px; }
  .hotel-line {
    position: absolute;
    left: 56px;
    bottom: 46px;
    font-size: 16px;
    letter-spacing: 0.1em;
    text-transform: uppercase;
  }
</style>
</head>
<body>
  <main class="canvas">
    <section class="card card-front" aria-label="Business card front">
      <div class="brand-square"></div>
      <div class="brand-name">Corvale Terrace<br>Hotel</div>
    </section>

    <section class="card card-back" aria-label="Business card back">
      <div class="contact">
        <p class="contact-name">Elias Navarro</p>
        <p class="contact-role">CEO/Founder</p>
        <p class="contact-lines">Lindwell Banca Avenue corner Tolenta St<br>Cebu City 6000 Philippines</p>
        <p class="contact-lines">p. +63 32 481 7302<br>c. +63 917 648 2095</p>
        <p class="contact-lines">stay@corvaleterracehotel.example<br>www.corvaleterracehotel.example</p>
      </div>
      <p class="hotel-line">Corvale Terrace Hotel</p>
    </section>
  </main>
</body>
</html>
```